New Company Business Card design

Looking for a corporate looking business card utilising my new logo design - the logo i would like embossed as one option and flat as another - simplistic but stylish - less is more - we are an import export business launching into the market - i would like a couple of options as main background - Grey or Black

```html
<!DOCTYPE html>
<html lang="en">
<head>
<meta charset="utf-8">
<title>Meridian Trade Partners – Business Card</title>
<link rel="stylesheet" href="https://fonts.googleapis.com/css2?family=Cinzel:wght@500&family=Arimo:wght@400&display=swap">
<style>
  :root {
    --backdrop: #666666;
    --card: #f0f0f0;
    --pattern-light: #e4e4e4;
    --pattern-dark: #d6d6d6;
    --brand-blue: #1f73bf;
    --ink: #4a4a4a;
    --rule: #c9c9c9;
    --tag-grey: #7a7a7a;
  }
  * { margin: 0; padding: 0; box-sizing: border-box; }
  html, body { width: 1200px; height: 802px; overflow: hidden; }
  body { background: var(--backdrop); position: relative; font-family: "Arimo", Arial, sans-serif; }

  .card {
    position: absolute; top: 274px; width: 443px; height: 265px;
    background: var(--card); overflow: hidden;
  }
  .card--front { left: 136px; }
  .card--back { left: 624px; }

  /* Front */
  .front-mark {
    position: absolute; left: 34px; top: 98px; width: 160px;
    font-family: "Cinzel", Georgia, serif; font-weight: 500;
    font-size: 58px; line-height: 1; color: var(--brand-blue);
    text-align: center; letter-spacing: 1px;
  }
  .front-divider {
    position: absolute; left: 206px; top: 61px; width: 1px; height: 132px;
    background: var(--rule);
  }
  .contact-block { position: absolute; left: 222px; top: 76px; }
  .holder-name {
    font-family: "Cinzel", Georgia, serif; font-weight: 500;
    font-size: 17px; color: var(--brand-blue); letter-spacing: .5px; line-height: 1.2;
  }
  .holder-role { font-size: 13px; color: var(--ink); margin-top: 1px; }
  .contact-list { list-style: none; margin-top: 18px; }
  .contact-list li {
    display: flex; align-items: center; gap: 3px;
    font-size: 13px; color: var(--ink); line-height: 16px;
  }
  .contact-list svg { width: 10px; height: 10px; fill: var(--brand-blue); flex: none; }

  /* Back */
  .back-pattern {
    position: absolute; inset: 0;
    background: linear-gradient(135deg, var(--pattern-light), var(--pattern-dark));
  }
  .back-brand {
    position: absolute; left: 0; right: 0; top: 108px; text-align: center;
  }
  .company-name {
    font-family: "Cinzel", Georgia, serif; font-weight: 500;
    font-size: 24px; line-height: 1.2; color: var(--brand-blue); letter-spacing: .8px;
  }
  .tagline {
    font-family: "Arimo", Arial, sans-serif; font-size: 8.5px; color: var(--tag-grey);
    letter-spacing: 2.4px; margin-top: 14px;
  }
</style>
</head>
<body>
  <section class="card card--front" aria-label="Business card front">
    <div class="front-mark">MTP</div>
    <div class="front-divider"></div>
    <div class="contact-block">
      <p class="holder-name">DANIEL HARGROVE</p>
      <p class="holder-role">Managing Director</p>
      <ul class="contact-list">
        <li><svg viewBox="0 0 10 10"><path d="M1 4c0-2 8-2 8 0v1H7V4H3v1H1zM2 6h6l1 3H1z"/></svg>021-555 018 240</li>
        <li><svg viewBox="0 0 10 10"><path d="M3 0h4a1 1 0 0 1 1 1v8a1 1 0 0 1-1 1H3a1 1 0 0 1-1-1V1a1 1 0 0 1 1-1zm0 1.5v6h4v-6z"/></svg>021-555 018 241</li>
        <li><svg viewBox="0 0 10 10"><path d="M0 2h10v6H0zm1 1v.3l4 2.5 4-2.5V3z"/></svg>hello@meridiantp.com</li>
        <li><svg viewBox="0 0 10 10"><circle cx="5" cy="5" r="4.5"/></svg>www.meridiantp.com</li>
      </ul>
    </div>
  </section>

  <section class="card card--back" aria-label="Business card back">
    <div class="back-pattern" role="img" aria-label="Faint repeating brand pattern in white on light grey"></div>
    <div class="back-brand">
      <p class="company-name">MERIDIAN TRADE PARTNERS</p>
      <p class="tagline">WORLDWIDE TRADE FOR EVERYDAY DEMAND</p>
    </div>
  </section>
</body>
</html>
```